Maplecrest Disability - Social Security Disability Attorneys

Our company is expanding to attract clients nationwide for our social security disability practice. We have a logo, but I am looking for a creative and elegant letterhead that projects an image of being technologically advanced but still professional enough for the legal field. I am looking for the "wow factor" combined with this is still professional enough for a law practice.

Requesting letterhead and business card design
Updates

Had to update and change the logo. The previous logo had a typo. Please send updates with the new logo for consideration. The letterhead and business cards should be professional enough to be used for a law firm. Thanks.

Industry/Entity Type

Law Practice, Law Firm, Healthcare Industry, Government

Colors

Designer to choose colors to be used in the design.

Requirements
Nice to have
• **Please create a vertical design for the business card**

```html
<!DOCTYPE html>
<html lang="en">
<head>
<meta charset="utf-8">
<title>Maplecrest Disability – Business Card</title>
<link rel="stylesheet" href="https://fonts.googleapis.com/css2?family=Cinzel:wght@700&family=Mulish:wght@400;600&display=swap">
<style>
  :root {
    --backdrop: #c9c9c9;
    --card-white: #f7f7f8;
    --brand-blue: #0a7fdc;
    --brand-blue-deep: #0a62d6;
    --brand-sky: #0c9ee0;
    --brand-orange: #e86f0c;
    --card-black: #161616;
    --text-white: #ffffff;
  }
  * { box-sizing: border-box; margin: 0; padding: 0; }
  html, body { width: 1200px; height: 800px; overflow: hidden; }
  body {
    background: var(--backdrop);
    display: flex;
    align-items: center;
    justify-content: center;
    gap: 60px;
  }
  .card {
    position: relative;
    width: 520px;
    height: 297px;
    border-radius: 22px;
    overflow: hidden;
  }
  .card--front { background: var(--card-white); }
  .card--back {
    background: var(--card-black);
    display: flex;
    align-items: center;
    justify-content: center;
  }
  .card__band { position: absolute; inset: 0; }
  .holder {
    position: absolute;
    top: 28px;
    right: 40px;
    text-align: left;
  }
  .holder__name {
    font-family: 'Cinzel', serif;
    font-weight: 700;
    font-size: 22px;
    line-height: 1.3;
    color: var(--brand-blue-deep);
    letter-spacing: 0.5px;
  }
  .holder__role {
    font-family: 'Mulish', sans-serif;
    font-size: 14px;
    line-height: 1.3;
    color: var(--brand-orange);
    margin-top: 2px;
    padding-left: 60px;
  }
  .contact {
    position: absolute;
    left: 30px;
    bottom: 14px;
    font-family: 'Mulish', sans-serif;
    font-size: 12.5px;
    line-height: 1.45;
    color: var(--text-white);
    list-style: none;
  }
  .contact__row { display: flex; align-items: center; gap: 8px; }
  .contact__row--plain { padding-left: 20px; }
  .contact__icon { width: 12px; height: 12px; flex: none; }
  .wordmark {
    font-family: 'Cinzel', serif;
    font-weight: 700;
    font-size: 34px;
    color: var(--brand-blue);
    letter-spacing: 1px;
    text-transform: uppercase;
  }
</style>
</head>
<body>
  <section class="card card--front">
    <svg class="card__band" viewBox="0 0 520 297" preserveAspectRatio="none" aria-hidden="true">
      <defs>
        <linearGradient id="bandFill" x1="0" y1="1" x2="1" y2="0">
          <stop offset="0" stop-color="#0a62d6"/>
          <stop offset="1" stop-color="#0c9ee0"/>
        </linearGradient>
      </defs>
      <path d="M0,165 Q240,90 520,100 L520,297 L0,297 Z" fill="url(#bandFill)"/>
      <path d="M0,178 Q240,110 520,120" fill="none" stroke="var(--brand-orange)" stroke-width="9"/>
      <path d="M0,194 Q240,126 520,136" fill="none" stroke="#ffffff" stroke-width="1.2"/>
    </svg>

    <div class="holder">
      <p class="holder__name">Daniel Whitford</p>
      <p class="holder__role">Founder &amp; CEO</p>
    </div>

    <ul class="contact">
      <li class="contact__row contact__row--plain">2140 Cedar Hollow Road</li>
      <li class="contact__row contact__row--plain">Juneau, Alaska 99801</li>
      <li class="contact__row">
        <svg class="contact__icon" viewBox="0 0 12 12" aria-hidden="true"><path d="M2.5 1 L4.5 1 L5.2 3.5 L4 4.5 Q5 7 7.5 8 L8.5 6.8 L11 7.5 L11 9.5 Q10 11 8 11 Q1 9 1 3 Q1 1.5 2.5 1 Z" fill="#fff"/></svg>
        555-218-4470
      </li>
      <li class="contact__row">
        <svg class="contact__icon" viewBox="0 0 12 12" aria-hidden="true"><rect x="0.5" y="2.5" width="11" height="7.5" rx="1" fill="#fff"/><path d="M1 3 L6 7 L11 3" fill="none" stroke="#0a6ad8" stroke-width="1"/></svg>
        info@maplecrestdisability.com
      </li>
      <li class="contact__row">
        <svg class="contact__icon" viewBox="0 0 12 12" aria-hidden="true"><circle cx="6" cy="6" r="5.5" fill="#fff"/><path d="M0.8 6 H11.2 M6 0.5 Q3 6 6 11.5 M6 0.5 Q9 6 6 11.5" fill="none" stroke="#0a6ad8" stroke-width="0.9"/></svg>
        www.maplecrestdisability.com
      </li>
    </ul>
  </section>

  <section class="card card--back">
    <p class="wordmark">Maplecrest Disability</p>
  </section>
</body>
</html>
```